Popup Nightclub Grand Opening Flyer

We need to design a flyer for the grand opening of an upscale, exclusive nightclub called "Lantern". The design needs to be chic and exclusive. The background should be black and the text should primarily be white. We like minimalist designs.

Here is the text for the flyer
-
Velvetroll Atlanta Presents

Lantern (LOGO)

A Popup Nightclub Experience
For one night Only

Friday, October 18, 2013
Party begins at 9PM

INVITE ONLY

See invitation for location details
(Velvetroll Atlanta logo)

-
Examples we like

http://cdn4-x.pressfolio-example.com/sites/default/files/styles/image_content_width/hash/3b/fd/2468013579_4421_flyer.jpg?itok=K9rtQw2z

http://files.hubspace-example.net/files/8Hqq-Tr72WWE3kaRbTmcxP5QZK2F396J8nbRw4CKMHfdX2Y7qSEF-MqjxDoNrLY3QCyQJD7npjGaRq3k-Mhx6hqf3MDSWf8r3/2zenSaturdays.jpg

http://morvex-example.com/wp-content/uploads/siteskin/widgetkit/gallery/2zen/2zen-gen_qstay4-01.jpg

Hi All, one thing that we are seeing that we don't like is on over emphasis on the phrase "a popup nightclub experience" please don't make this the largest thing on the flyer

Target Market(s)

Target market is 25-35 year olds who are affluent (rich) and like luxury brands

Requirements
Must have
• Dark Background
Nice to have
• Velvetroll Logo on the bottom
Modern text that isn't curvy
Should not have
• Curved text

```html
<!DOCTYPE html>
<html lang="en">
<head>
<meta charset="utf-8">
<title>Lantern Nightclub – Popup Opening Flyer</title>
<link rel="stylesheet" href="https://fonts.googleapis.com/css2?family=Jost:wght@300;400;600&display=swap">
<style>
  :root {
    --night: #000000;
    --ink: #e4edf8;
    --glow: rgba(150, 195, 255, 0.75);
    --ember: #c8281a;
    --flame: #f0552a;
  }
  * { margin: 0; padding: 0; box-sizing: border-box; }
  html, body {
    width: 1200px; height: 1080px; overflow: hidden; background: var(--night);
  }
  .flyer {
    position: relative; width: 1200px; height: 1080px; overflow: hidden;
    background: var(--night);
    font-family: "Jost", "Futura", sans-serif;
    color: var(--ink);
  }
  .backdrop {
    position: absolute; inset: 0;
    background: linear-gradient(172deg,
      var(--night) 0%, var(--night) 22%,
      #5a0c06 34%, var(--ember) 48%, var(--flame) 62%,
      #7a1206 76%, var(--night) 88%, var(--night) 100%);
  }
  .line {
    position: absolute; left: 0; width: 1200px; text-align: center;
    line-height: 1; text-transform: uppercase; white-space: nowrap;
    text-shadow: 0 0 8px var(--glow), 0 0 18px var(--glow);
  }
  .presents { top: 55px; font-size: 28px; font-weight: 400; letter-spacing: 3px; }
  .brand-mark {
    position: absolute; left: 540px; top: 162px; width: 120px; height: 120px;
    border-radius: 50%; background: var(--ink);
  }
  .brand-name {
    position: absolute; left: 0; width: 1200px; top: 342px; text-align: center;
    line-height: 1; font-size: 66px; font-weight: 300; letter-spacing: 12px;
    text-indent: 12px; color: var(--ink); text-transform: uppercase;
  }
  .brand-kind {
    position: absolute; left: 0; width: 1200px; top: 414px; text-align: center;
    line-height: 1; font-size: 34px; font-weight: 300; letter-spacing: 4px;
    text-indent: 4px; color: var(--ink); text-transform: uppercase;
  }
  .headline { font-size: 40px; font-weight: 600; letter-spacing: 2.5px; }
  .headline--one { top: 514px; }
  .headline--two { top: 568px; letter-spacing: 4px; }
  .rule {
    position: absolute; height: 3px; background: var(--ink);
    box-shadow: 0 0 8px var(--glow);
  }
  .rule--main { left: 330px; width: 518px; top: 626px; }
  .date { top: 649px; font-size: 42px; font-weight: 300; letter-spacing: 1.5px; }
  .time { top: 693px; font-size: 41px; font-weight: 400; letter-spacing: 4px; }
  .invite { top: 775px; font-size: 40px; font-weight: 600; letter-spacing: 1.5px; }
  .rule--left { left: 330px; width: 120px; top: 796px; }
  .rule--right { left: 732px; width: 116px; top: 796px; }
  .location { top: 872px; font-size: 29px; font-weight: 400; letter-spacing: 2.5px; }
  .host {
    position: absolute; top: 955px; left: 0; width: 1200px; height: 46px;
    display: flex; justify-content: center; align-items: center; gap: 20px;
  }
  .host-dot { width: 44px; height: 44px; border-radius: 50%; background: #ffffff; }
  .host-name {
    font-size: 44px; font-weight: 300; letter-spacing: 3px; line-height: 1;
    color: #ffffff; text-transform: uppercase;
  }
</style>
</head>
<body>
<main class="flyer">
  <div class="backdrop" role="img" aria-label="Flowing red and orange light-wave artwork across a black background"></div>

  <p class="line presents">Velvetroll Atlanta Presents</p>

  <div class="brand-mark"></div>
  <h1 class="brand-name">Lantern</h1>
  <p class="brand-kind">Nightclub</p>

  <p class="line headline headline--one">A Popup Nightclub Experience</p>
  <p class="line headline headline--two">For One Night Only</p>
  <div class="rule rule--main"></div>

  <p class="line date">Friday, October 18, 2013</p>
  <p class="line time">Party Begins at 9PM</p>

  <div class="rule rule--left"></div>
  <p class="line invite">Invite Only</p>
  <div class="rule rule--right"></div>

  <p class="line location">See Invitation for Location Details</p>

  <div class="host">
    <span class="host-dot"></span>
    <span class="host-name">Velvetroll</span>
  </div>
</main>
</body>
</html>
```